Brell Stone Company Business Cards

Front and Back Business Card - logo and text setup - cool design. I need workable photoshop or illustrator files so I can setup each employee card with design that is created
Updates

Hi everyone, thank you for the great entries. Please no more white and blue cards - there are so many already - black and silver only now please. thanks!

Target Market(s)

Construction Industry - Facility Managers

Industry/Entity Type

Construction

Contact Information for Business Card

I really like contemporary simplistic looks - clean neat....not opposed to seeing some black backrounds

Requirements
Must have
• Logo/website address with design on front only - www.brellstone-example.com (logo attached)
• Back:
• Name/Title/Company Address/Phone/email address
Nice to have
• Cool design
Should not have
• Nothing gimmicky like Fire or Water - since we are a Fire Protection company - it has all been done

```html
<!DOCTYPE html>
<html lang="en">
<head>
<meta charset="utf-8">
<title>Brell Stone Company Business Cards</title>
<link rel="stylesheet" href="https://fonts.googleapis.com/css2?family=Open+Sans:wght@400;700;800&display=swap">
<style>
  :root {
    --stage: #c9ccd0;
    --card: #000000;
    --brand-blue: #0a25a0;
    --band-blue: #0424a0;
    --accent-green: #6a8a3a;
    --ink-light: #ffffff;
    --logo-grey: #6e6e6e;
  }
  * { margin: 0; padding: 0; box-sizing: border-box; }
  html, body { width: 1200px; height: 1193px; overflow: hidden; }
  body {
    background: var(--stage);
    font-family: "Open Sans", sans-serif;
    position: relative;
  }
  .card {
    position: absolute;
    width: 860px;
    height: 500px;
    background: var(--card);
    border-radius: 38px;
    overflow: hidden;
  }
  .card--front { left: 250px; top: 60px; }
  .card--back { left: 90px; top: 630px; }

  .brand-name {
    position: absolute;
    left: 0; right: 0;
    text-align: center;
    font-weight: 800;
    letter-spacing: -2px;
    line-height: 1;
  }
  .card--front .brand-name { top: 70px; font-size: 92px; color: var(--brand-blue); }
  .card--back .brand-name { top: 170px; font-size: 110px; color: var(--logo-grey); }

  .holder {
    position: absolute;
    top: 250px; left: 0; right: 0;
    text-align: center;
    color: var(--ink-light);
    font-size: 30px;
  }
  .holder__name { font-weight: 700; }
  .holder__title { font-weight: 400; }

  .band { position: absolute; left: 0; top: 0; width: 860px; height: 500px; }

  .contact {
    position: absolute;
    left: 0; right: 0; top: 375px;
    color: var(--ink-light);
    font-size: 25px;
    text-align: center;
    line-height: 1.45;
  }
  .contact__row { display: flex; justify-content: center; align-items: center; gap: 30px; }
  .contact__item { display: inline-flex; align-items: center; gap: 10px; }
  .contact__item svg { width: 26px; height: 26px; fill: none; stroke: var(--ink-light); stroke-width: 2; }
  .contact__item svg.solid { fill: var(--ink-light); stroke: none; }
  .contact__address { margin-top: 4px; }

  .web-spaced {
    position: absolute;
    left: 0; right: 0; top: 320px;
    text-align: center;
    color: var(--ink-light);
    font-size: 28px;
    letter-spacing: 7px;
  }
</style>
</head>
<body>

  <section class="card card--front" aria-label="Business card contact side">
    <div class="brand-name">Brell Stone</div>
    <p class="holder"><span class="holder__name">Maren Castell,</span> <span class="holder__title">President</span></p>

    <svg class="band" viewBox="0 0 860 500" aria-hidden="true">
      <path d="M0 345 Q430 230 860 400" fill="none" stroke="var(--accent-green)" stroke-width="6"/>
      <path d="M0 352 Q430 240 860 408 L860 500 L0 500 Z" fill="var(--band-blue)"/>
    </svg>

    <div class="contact">
      <div class="contact__row">
        <span class="contact__item">
          <svg class="solid" viewBox="0 0 24 24"><path d="M6.6 10.8a15 15 0 0 0 6.6 6.6l2.2-2.2a1 1 0 0 1 1-.25 11.4 11.4 0 0 0 3.6.57 1 1 0 0 1 1 1V20a1 1 0 0 1-1 1A17 17 0 0 1 3 4a1 1 0 0 1 1-1h3.5a1 1 0 0 1 1 1c0 1.25.2 2.45.57 3.57a1 1 0 0 1-.25 1z"/></svg>
          (555) 014-2290
        </span>
      </div>
      <div class="contact__row">
        <span class="contact__item">
          <svg viewBox="0 0 24 24"><rect x="2.5" y="5" width="19" height="14"/><path d="M2.5 5l9.5 8 9.5-8M2.5 19l7-7M21.5 19l-7-7"/></svg>
          info@brellstone-example.com
        </span>
        <span class="contact__item">
          <svg viewBox="0 0 24 24"><circle cx="12" cy="12" r="9.5"/><ellipse cx="12" cy="12" rx="4" ry="9.5"/><path d="M2.5 12h19M4 7h16M4 17h16"/></svg>
          www.brellstone-example.com
        </span>
      </div>
      <p class="contact__address">48 Harbor Works Lane, Northfield, NY 10000</p>
    </div>
  </section>

  <section class="card card--back" aria-label="Business card brand side">
    <div class="brand-name">Brell Stone</div>
    <p class="web-spaced">www.brellstone-example.com</p>
  </section>

</body>
</html>
```